Dietitian needs awesome business card

I need a contemporary design that's eye catching but professional.
My card is to given to doctors, specialists and patients alike.
I manage patients with chronic diseases
I have uploaded my logo and current business card, I would also like the other Certified Clinical Nutritionist logo incorporated into the design

Target Market(s)

Doctors, specialists and patients

Industry/Entity Type

Healthcare

Contact Information for Business Card

www.brightfieldnutrition.com.au
Ph: 0427 561 903
Fax: 6457 2183
email: marcus.k.diet@fernmail.com
Space on the back of the card with: Appointment date, Appointment time and appointment location

Font styles to use
Serif

Colors
fbee3e
876aae
ffc214

Requirements
Must have
• My Logo
• Certified Clinical Nutritionist Logo
• My 4 locations - Pinebrook Medical Centre, North Corrin Health, Hollis Medical, Ashcombe Doctors Surgery
Nice to have
• I like the colours in my current business card

```html
<!DOCTYPE html>
<html lang="en">
<head>
<meta charset="utf-8">
<title>Brightfield Nutrition &amp; Dietetics – Business Card</title>
<link rel="stylesheet" href="https://fonts.googleapis.com/css2?family=Philosopher:wght@400;700&family=Sarabun:wght@400;500&display=swap">
<style>
  :root {
    --bg: #8c8c8c;
    --card: #ffffff;
    --navy: #283a8f;
    --green: #8cc63f;
    --ink: #4a4a4a;
    --rule: #9a9a9a;
    --badge: #f47b20;
  }
  * { box-sizing: border-box; margin: 0; padding: 0; }
  html, body { width: 1105px; height: 1200px; overflow: hidden; }
  body { background: var(--bg); position: relative; font-family: "Sarabun", sans-serif; color: var(--ink); }

  .card { position: absolute; left: 182px; width: 746px; height: 427px; background: var(--card); }
  .card--front { top: 119px; }
  .card--back { top: 636px; }

  /* Front */
  .brand { position: absolute; top: 52px; right: 38px; display: flex; align-items: center; gap: 14px; }
  .brand__dot { width: 72px; height: 72px; border-radius: 50%; background: var(--green); flex: none; }
  .brand__name { font-family: "Philosopher", serif; color: var(--navy); font-size: 30px; line-height: 1.1; }

  .person { position: absolute; left: 39px; top: 200px; }
  .person__name { font-family: "Philosopher", serif; font-size: 28px; color: var(--navy); font-weight: 400; line-height: 1.2; }
  .person__role { font-size: 20px; color: var(--green); line-height: 1.4; }

  .contacts { position: absolute; left: 39px; top: 280px; list-style: none; }
  .contacts li { display: flex; align-items: center; gap: 10px; font-size: 19px; height: 29px; }
  .contacts svg { width: 18px; height: 18px; fill: var(--navy); flex: none; }

  /* Back */
  .back-mark { position: absolute; left: 48px; top: 40px; width: 84px; height: 84px; border-radius: 50%; background: var(--green); }
  .badge { position: absolute; left: 515px; top: 41px; width: 178px; height: 83px; background: var(--badge); display: flex; align-items: center; justify-content: space-between; padding: 0 12px 0 10px; }
  .badge__text { color: #fff; font-size: 14px; line-height: 1.2; width: 90px; }
  .badge__seal { width: 62px; height: 62px; border-radius: 50%; background: #fff; }

  .notes { position: absolute; left: 50px; width: 643px; top: 168px; }
  .notes__line { height: 1px; background: var(--rule); margin-bottom: 40px; }

  .appt { position: absolute; left: 50px; top: 278px; width: 643px; display: flex; align-items: baseline; color: var(--navy); font-size: 20px; }
  .appt__label { margin-right: 12px; }
  .appt__fill { border-bottom: 2px dotted var(--navy); height: 1px; align-self: center; margin-top: 8px; }
  .appt__fill--date { flex: 1; margin-right: 10px; }
  .appt__fill--time { width: 140px; margin-right: 8px; }
  .appt__ampm { font-size: 15px; }

  .locations { position: absolute; left: 50px; top: 330px; width: 650px; display: grid; grid-template-columns: 375px 1fr; row-gap: 4px; list-style: none; }
  .locations li { display: flex; align-items: center; gap: 10px; font-size: 20px; height: 29px; }
  .locations .box { width: 16px; height: 16px; border: 1.5px solid var(--navy); flex: none; }
</style>
</head>
<body>

<section class="card card--front" aria-label="Card front">
  <div class="brand">
    <span class="brand__dot"></span>
    <span class="brand__name">Brightfield<br>Nutrition &amp; Dietetics</span>
  </div>

  <div class="person">
    <h1 class="person__name">Marcus Kellerman</h1>
    <p class="person__role">Nutritionist &amp; Chef</p>
  </div>

  <ul class="contacts">
    <li>
      <svg viewBox="0 0 24 24" aria-hidden="true"><path d="M6.6 10.8a15.2 15.2 0 0 0 6.6 6.6l2.2-2.2a1 1 0 0 1 1-.25 11.4 11.4 0 0 0 3.6.57 1 1 0 0 1 1 1V20a1 1 0 0 1-1 1A17 17 0 0 1 3 4a1 1 0 0 1 1-1h3.5a1 1 0 0 1 1 1c0 1.25.2 2.45.57 3.6a1 1 0 0 1-.25 1z"/></svg>
      0427 561 903
    </li>
    <li>
      <svg viewBox="0 0 24 24" aria-hidden="true"><path d="M6 2h10v5H6zM3 8h18a1 1 0 0 1 1 1v8h-4v4H6v-4H2V9a1 1 0 0 1 1-1zm5 8v3h8v-3z"/></svg>
      6457 2183
    </li>
    <li>
      <svg viewBox="0 0 24 24" aria-hidden="true"><path d="M2 5h20v14H2zm2 2v.5l8 5 8-5V7zm0 3v7h16v-7l-8 5z"/></svg>
      marcus.k.diet@fernmail.com
    </li>
    <li>
      <svg viewBox="0 0 24 24" aria-hidden="true"><path d="M12 2a10 10 0 1 0 0 20 10 10 0 0 0 0-20zm-1 17.9A8 8 0 0 1 4.2 10L9 14.8v1a2 2 0 0 0 2 2zm6.9-2.5A2 2 0 0 0 16 16h-1v-3a1 1 0 0 0-1-1H8v-2h2a1 1 0 0 0 1-1V7h2a2 2 0 0 0 2-2v-.4a8 8 0 0 1 2.9 12.8z"/></svg>
      brightfieldnutrition.com.au
    </li>
  </ul>
</section>

<section class="card card--back" aria-label="Card back">
  <span class="back-mark"></span>

  <div class="badge">
    <span class="badge__text">Certified Clinical Nutritionist</span>
    <span class="badge__seal"></span>
  </div>

  <div class="notes">
    <div class="notes__line"></div>
    <div class="notes__line"></div>
    <div class="notes__line"></div>
  </div>

  <div class="appt">
    <span class="appt__label">Date :</span>
    <span class="appt__fill appt__fill--date"></span>
    <span class="appt__label">Time :</span>
    <span class="appt__fill appt__fill--time"></span>
    <span class="appt__ampm">AM/PM</span>
  </div>

  <ul class="locations">
    <li><span class="box"></span>Pinebrook Medical Centre</li>
    <li><span class="box"></span>Ashcombe Doctors Surgery</li>
    <li><span class="box"></span>North Corrin Health</li>
    <li><span class="box"></span>Hollis Medical</li>
  </ul>
</section>

</body>
</html>
```